Property Finance Company - Orbin Funding Limited

Background: Orbin Funding Group Limited is a private property finance company. Orbin Funding Group has capital to directly fund first mortgage, mezzanine and preferred equity financing. We also acquire performing, sub-performing and distressed debt.

Orbin Fundings management philosophy emphasises expertise, innovation, wisdom, honesty and competitiveness. Orbin Funding are not finance brokers - we provide debt funding to the commercial property and residential development sectors. Our process is built from experience and cumutavely Orbin Fundings Directors have in excess of 60 years wisdom.

The aim of the website will be to increase brand awareness, provide clients with comfort around our level of skill and background on who we are, generate more sales, and provide examples of projects that we have funded.

The website is a new product launch, and we need to use our Orbin Funding logo that has just been designed. We like a dark background, and either black/silver/grey/ jade green, or black/gold/jade green colours.

Our unique advantages are that we have fast turnaround times, we can solve clients funding problems and we know what we are doing. Our target audience will be viewing the website on both desktop and mobile devices.

We would like to have the following pages:

Home
About
Team
Services
Project Experience
Contact

Competitors Website: http://www.tarvolo.example/

We would also like to have the option of video footage in our website, as you can see in our competitors website.

Overall we want a really slick, elegant but modern website that is better than www.tarvolo.example

Target Market(s)

Finance borrowers, property developers, accountants, lawyers, businesspeople, high net worth people

Industry/Entity Type

Finance

Requirements
Must have
• Please see project description
Nice to have
Should not have

```html
<!DOCTYPE html>
<html lang="en">
<head>
<meta charset="utf-8">
<title>Orbin Funding Group</title>
<link rel="stylesheet" href="https://fonts.googleapis.com/css2?family=Lato:wght@300;400;700;900&family=Open+Sans:wght@400;600;700&display=swap">
<style>
:root{
  --jade:#0aa865;
  --jade-dark:#08945a;
  --ink:#222528;
  --text:#4a4a4a;
  --muted:#6b6b6b;
  --line:#e3e3e3;
  --card:#e6e6e6;
  --white:#ffffff;
  --hero-top:#4a5770;
  --hero-bottom:#2a2e3a;
}
*{box-sizing:border-box;margin:0;padding:0}
html,body{width:1200px;height:2253px;overflow:hidden}
body{position:relative;background:var(--white);font-family:"Lato",sans-serif;color:var(--text)}
.abs{position:absolute}

/* hero */
.hero{left:0;top:0;width:1200px;height:583px;background:linear-gradient(180deg,#54607a 0%,#6e6a78 30%,#4b4f5e 62%,#2b2d36 100%)}
.hero-photo{left:0;top:0;width:1200px;height:583px;background:radial-gradient(ellipse 380px 520px at 610px 330px,rgba(40,46,60,.75),rgba(40,46,60,0) 70%),linear-gradient(90deg,rgba(150,110,100,.25),rgba(0,0,0,0) 40%,rgba(0,0,0,0) 70%,rgba(60,80,120,.25))}
.hero-brand{left:92px;top:86px;color:var(--white);font-size:25px;font-weight:400;letter-spacing:1px;text-align:center;line-height:1.1}
.hero-brand small{display:block;font-size:15px;letter-spacing:4px}
.menu-btn{left:1070px;top:26px}
.story{left:98px;top:398px;display:flex;align-items:center;gap:14px;color:var(--white)}
.story-title{font-size:42px;font-weight:400;letter-spacing:.5px;line-height:1}
.story-sub{font-size:16px;letter-spacing:1px;margin-top:8px;margin-left:8px}
.scroll-down{left:588px;top:514px}

/* nav */
.nav{left:0;top:583px;width:1200px;height:104px;border-bottom:1px solid var(--line);background:var(--white)}
.nav-brand{left:100px;top:30px;display:flex;align-items:center;gap:12px;color:#5a5a5a;font-size:24px;letter-spacing:1px}
.nav-brand .mark{width:40px;height:40px;border-radius:50%;background:#8a8a8a}
.nav-links{right:100px;top:40px;display:flex;gap:38px;font-family:"Open Sans",sans-serif;font-size:15px;color:#444;list-style:none}

/* about */
.about-title{left:100px;top:722px;font-size:37px;color:var(--ink);font-weight:400;letter-spacing:.5px}
.about-title b,.section-title b{font-weight:900}
.about-rule{left:343px;top:723px;width:1px;height:130px;background:var(--line)}
.about-text{left:373px;top:726px;width:728px;font-family:"Open Sans",sans-serif;font-size:12px;line-height:20px;color:#555}
.about-text p+p{margin-top:12px}

.section-title{left:0;width:1200px;text-align:center;font-size:37px;color:var(--ink);font-weight:400;letter-spacing:.5px}

/* services */
.service{top:997px;width:322px;height:209px;padding:24px 0 0}
.service h3{font-family:"Open Sans",sans-serif;font-size:16px;font-weight:600;color:var(--ink);margin-top:18px;letter-spacing:.3px}
.service p{font-family:"Open Sans",sans-serif;font-size:12px;line-height:15px;color:#666;margin-top:14px;text-align:justify}
.service.active{background:linear-gradient(135deg,var(--jade) 60%,var(--jade-dark));padding:24px 24px 0}
.service.active h3,.service.active p{color:var(--white)}

/* projects */
.project{top:1322px;width:324px;height:351px;background:var(--card);text-align:center}
.project-photo{width:324px;height:210px;position:relative}
.project h3{font-family:"Open Sans",sans-serif;font-size:17px;font-weight:600;color:var(--ink);margin-top:16px;letter-spacing:.3px}
.project p{font-family:"Open Sans",sans-serif;font-size:12px;line-height:15px;color:#555;margin:16px 28px 0}
.read-more{position:absolute;left:113px;top:90px;background:var(--jade);color:var(--white);font-family:"Open Sans",sans-serif;font-size:11px;font-weight:600;padding:6px 10px;border-radius:8px;letter-spacing:.3px}

/* cta */
.cta{left:100px;top:1703px;width:1001px;height:239px;background:linear-gradient(180deg,#1f7f8c 0%,#2a8f98 45%,#1f6a70 100%)}
.cta-text{left:51px;top:84px;width:640px;color:var(--white);font-family:"Open Sans",sans-serif;font-size:21.5px;font-weight:600;line-height:30px}
.cta-btn{left:770px;top:92px;width:185px;height:41px;background:var(--white);border-radius:6px;color:var(--jade);font-family:"Open Sans",sans-serif;font-size:16px;font-weight:600;text-align:center;line-height:41px;letter-spacing:.3px}

/* footer */
.footer-col h4{font-family:"Open Sans",sans-serif;font-size:17px;font-weight:400;color:var(--ink)}
.contact-list{list-style:none;font-family:"Open Sans",sans-serif;font-size:12px;color:#333;margin-top:20px}
.contact-list li{display:flex;gap:14px;align-items:flex-start;line-height:31px}
.contact-list svg{margin-top:10px;flex:none}
.nav-list{list-style:none;font-family:"Open Sans",sans-serif;font-size:12px;color:#333;margin-top:22px;line-height:32px}
.news-note{font-family:"Open Sans",sans-serif;font-size:12px;color:#333;margin-top:22px}
.news-form{display:flex;margin-top:16px;width:318px;height:43px}
.news-input{flex:1;background:#ebebeb;display:flex;align-items:center;gap:12px;padding-left:14px;font-family:"Open Sans",sans-serif;font-size:12px;color:#444}
.news-btn{width:107px;background:var(--jade);color:var(--white);font-family:"Open Sans",sans-serif;font-size:12px;text-align:center;line-height:43px;letter-spacing:.5px}
.socials{display:flex;gap:7px;margin-top:21px}
.socials span{width:38px;height:38px;border-radius:50%;display:block}
.bottom-bar{left:0;top:2210px;width:1200px;height:43px;background:var(--jade);color:var(--white);font-family:"Open Sans",sans-serif;font-size:12px;text-align:center;line-height:43px}
</style>
</head>
<body>

<header>
  <div class="abs hero" role="img" aria-label="Dusk photograph of a tall glass office tower over a city skyline"></div>
  <div class="abs hero-photo"></div>
  <div class="abs hero-brand">ORBIN FUNDING<small>GROUP</small></div>
  <svg class="abs menu-btn" width="32" height="22" viewBox="0 0 32 22" aria-label="Menu">
    <g stroke="#fff" stroke-width="2"><line x1="2" y1="2" x2="30" y2="2"/><line x1="10" y1="11" x2="30" y2="11"/><line x1="2" y1="20" x2="30" y2="20"/></g>
  </svg>
  <div class="abs story">
    <svg width="68" height="68" viewBox="0 0 68 68" aria-hidden="true">
      <circle cx="34" cy="34" r="34" fill="rgba(255,255,255,.45)"/>
      <path d="M27 20 L48 34 L27 48 Z" fill="#fff"/>
    </svg>
    <div>
      <div class="story-title">OUR STORY</div>
      <div class="story-sub">PLAY NOW</div>
    </div>
  </div>
  <svg class="abs scroll-down" width="24" height="14" viewBox="0 0 24 14" aria-label="Scroll down">
    <path d="M2 2 L12 12 L22 2" fill="none" stroke="#fff" stroke-width="2.5"/>
  </svg>

  <nav class="abs nav">
    <div class="abs nav-brand"><span class="mark"></span>ORBIN FUNDING GROUP</div>
    <ul class="abs nav-links">
      <li>Home</li><li>About</li><li>Team</li><li>Services</li><li>Project Experience</li><li>Contact</li>
    </ul>
  </nav>
</header>

<main>
  <h2 class="abs about-title"><b>ABOUT</b> US</h2>
  <div class="abs about-rule"></div>
  <div class="abs about-text">
    <p>Orbin Funding Group Limited is a private property finance company. Orbin Funding Group has capital to directly fund first mortgage, mezzanine and preferred equity financing. We also acquire performing, sub-performing and distressed debt.</p>
    <p>Orbin Fundings management philosophy emphasises expertise, innovation, wisdom, honesty and competitiveness. Orbin Funding are not finance brokers - we provide debt funding to the commercial property and residential development sectors. Our process is built from experience and cumutavely Orbin Fundings Directors have in excess of 60 years wisdom.</p>
  </div>

  <h2 class="abs section-title" style="top:925px"><b>OUR</b> SERVICES</h2>

  <div class="abs service" style="left:100px">
    <svg width="52" height="40" viewBox="0 0 52 40" aria-hidden="true">
      <g fill="none" stroke="#111" stroke-width="2">
        <rect x="10" y="2" width="40" height="24"/><rect x="6" y="6" width="40" height="24" fill="#fff"/><rect x="2" y="12" width="40" height="24" fill="#fff"/>
        <circle cx="22" cy="24" r="6"/><rect x="6" y="16" width="32" height="16"/>
      </g>
    </svg>
    <h3>DEBIT FUNDING</h3>
    <p>Sed ut perspiciatis unde omnis iste natus error sit voluptatem accusantium doloremque laudantium, totam</p>
  </div>

  <div class="abs service active" style="left:440px">
    <svg width="44" height="48" viewBox="0 0 44 48" aria-hidden="true">
      <g fill="none" stroke="#fff" stroke-width="2">
        <rect x="4" y="14" width="16" height="32"/><rect x="20" y="4" width="20" height="42"/>
        <line x1="0" y1="46" x2="44" y2="46"/>
        <path d="M8 20h8M8 26h8M8 32h8M24 10h12M24 16h12M24 22h12M24 28h12M24 34h12"/>
      </g>
    </svg>
    <h3>CAPITAL MANAGEMENT</h3>
    <p>Sed ut perspiciatis unde omnis iste natus error sit voluptatem accusantium doloremque laudantium, totam</p>
  </div>

  <div class="abs service" style="left:826px">
    <svg width="52" height="52" viewBox="0 0 52 52" aria-hidden="true">
      <circle cx="26" cy="26" r="24" fill="none" stroke="#111" stroke-width="2"/>
      <path d="M26 10 V26 H36" fill="none" stroke="#111" stroke-width="2.5"/>
      <g fill="#111"><circle cx="26" cy="6" r="1.5"/><circle cx="26" cy="46" r="1.5"/><circle cx="6" cy="26" r="1.5"/><circle cx="46" cy="26" r="1.5"/></g>
    </svg>
    <h3>OUR PROCESS</h3>
    <p>Sed ut perspiciatis unde omnis iste natus error sit voluptatem accusantium doloremque laudantium, totam</p>
  </div>

  <h2 class="abs section-title" style="top:1249px"><b>PROJECT</b> EXPERIENCES</h2>

  <article class="abs project" style="left:100px">
    <div class="project-photo" role="img" aria-label="Upward view of glass skyscrapers against a bright sky" style="background:linear-gradient(135deg,#3c4552 0%,#9aa6b4 45%,#e9eef3 60%,#5a6470 100%)">
      <span class="read-more">READ MORE</span>
    </div>
    <h3>LORIUM IPSUM</h3>
    <p>Sed ut perspiciatis unde omnis iste natus error sit voluptatem accusantium doloremque laudantium, totam</p>
  </article>

  <article class="abs project" style="left:439px">
    <div class="project-photo" role="img" aria-label="City skyline of office towers at sunset" style="background:linear-gradient(180deg,#3e4d6a 0%,#6b6f86 40%,#b86a5a 58%,#3a3c48 100%)"></div>
    <h3>LORIUM IPSUM</h3>
    <p>Sed ut perspiciatis unde omnis iste natus error sit voluptatem accusantium doloremque laudantium, totam</p>
  </article>

  <article class="abs project" style="left:778px">
    <div class="project-photo" role="img" aria-label="Downtown skyline glowing in golden morning light" style="background:linear-gradient(180deg,#f1e3c6 0%,#e8c28a 45%,#a8875f 75%,#6d5a44 100%)"></div>
    <h3>LORIUM IPSUM</h3>
    <p>Sed ut perspiciatis unde omnis iste natus error sit voluptatem accusantium doloremque laudantium, totam</p>
  </article>

  <section class="abs cta" role="img" aria-label="Teal-tinted night view of a city with a tall television tower">
    <p class="abs cta-text">Lorem ipsum dolor sit amet, consectetur adipiscing elit, sed do eiusmod tempor incididunt ut labore ...</p>
    <div class="abs cta-btn">CONTACT US</div>
  </section>
</main>

<footer>
  <div class="abs footer-col" style="left:103px;top:1966px">
    <h4>Contact Information</h4>
    <ul class="contact-list">
      <li><svg width="10" height="13" viewBox="0 0 10 13"><path d="M5 0a5 5 0 0 1 5 5c0 3-5 8-5 8S0 8 0 5a5 5 0 0 1 5-5z" fill="#333"/><circle cx="5" cy="5" r="1.8" fill="#fff"/></svg><span>Orbin Funding, Harbour City, 1st block<br>1234 Building no 8, floor 3</span></li>
      <li style="margin-top:10px"><svg width="12" height="9" viewBox="0 0 12 9"><rect x=".5" y=".5" width="11" height="8" fill="none" stroke="#333"/><path d="M.5 .5 6 5 11.5 .5" fill="none" stroke="#333"/></svg><span>Email:&nbsp; info@orbinfunding.example</span></li>
      <li><svg width="11" height="11" viewBox="0 0 11 11"><path d="M2 0l2 3-1 1.5c.8 1.6 1.9 2.7 3.5 3.5L8 7l3 2-1 2C5 11 0 6 0 1z" fill="#333"/></svg><span>Phone:&nbsp; 5550 123 456</span></li>
    </ul>
  </div>

  <div class="abs footer-col" style="left:508px;top:1966px">
    <h4>Navigation</h4>
    <ul class="nav-list">
      <li>Home</li><li>About us</li><li>Team</li><li>Services</li><li>Project Experience</li><li>Contact Us</li>
    </ul>
  </div>

  <div class="abs footer-col" style="left:789px;top:1966px">
    <h4>Newsletter</h4>
    <p class="news-note">Enter your email &amp; subcribing newsletter</p>
    <div class="news-form">
      <div class="news-input"><svg width="14" height="10" viewBox="0 0 14 10"><rect x=".5" y=".5" width="13" height="9" fill="none" stroke="var(--jade)"/><path d="M.5 .5 7 5.5 13.5 .5" fill="none" stroke="var(--jade)"/></svg>Email address</div>
      <div class="news-btn">SUBSCRIBE</div>
    </div>
    <div class="socials">
      <span style="background:#3b5998"></span>
      <span style="background:#4aaee6"></span>
      <span style="background:#dd4b39"></span>
    </div>
  </div>

  <div class="abs bottom-bar">© 2017 &nbsp;|&nbsp; www.orbinfunding.example</div>
</footer>

</body>
</html>
```